Business Card design for insurance broker in Denver, CO, USA

I need a business card designed using this logo that was just created. We sell life and disability income insurance to US consumers.
Looking for a professionally designed card to make use of the logo and have something to hand to prospects or new business referral sources. The card could be white, gray, black or whatever you would recommend.

Target Market(s)

US Consumers and other financial professionals that I partner with.

Industry/Entity Type

Insurance Broker

Contact Information for Business Card

Owen T. Farrow, CLU, LUTCF (please note that CLU should have a superscript R in a circle for registered trademark)
President
phone (303) 555-0187
email owen@keelbrookcover.example
4620 W. Halvern Rd, Suite 300, Greenwood Village, CO 80111
Somewhere fit in a tagline saying "Your resource for life, long term care, and disability insurance" (maybe the back if it doesn't fit on the front, your call)

Font styles to use
Sans Serif

Requirements
Must have
• Must have logo in correct blue and gray colors, my name, address, phone, email. Order and placement determined by the designer.
• I just want something that looks a more professional than what I could have done using the business card designer tool on pixelbazaar.example or QuillPress, or any other do-it-yourself tool
• A regular rectangular business card with square corners is preferred
Nice to have
• I included the logos of 2 organizations I belong to (GKLS and WOBCE). They should be small, but visible on the back only. If it doesn’t look good, this is not a requirement, feel free to drop it.
Should not have
• Do not add any colors not already in the logo, except use of black and whites which are okay. If you use the logo on the back and want to make that in all black, gray or white, that may be okay as well.

```html
<!DOCTYPE html>
<html lang="en">
<head>
<meta charset="utf-8">
<title>Keelbrook Cover – Business Card</title>
<link rel="stylesheet" href="https://fonts.googleapis.com/css2?family=Lato:wght@400;700&display=swap">
<style>
  :root {
    --page-bg: #111214;
    --card-bg: #24272b;
    --card-edge: #2c3034;
    --brand-blue: #1e88d0;
    --brand-gray: #a3a8ad;
    --text-gray: #b9bdc1;
    --rule-gray: #6b7075;
    --emboss: #3a3e43;
    --watermark: rgba(255, 255, 255, 0.035);
  }
  * { margin: 0; padding: 0; box-sizing: border-box; }
  html, body { width: 1200px; height: 800px; overflow: hidden; }
  body {
    background: var(--page-bg);
    font-family: "Lato", Arial, sans-serif;
    position: relative;
  }
  .card {
    position: absolute;
    width: 560px;
    height: 320px;
    background: var(--card-bg);
    border: 1px solid var(--card-edge);
    box-shadow: 0 18px 40px rgba(0, 0, 0, 0.55);
    overflow: hidden;
  }
  .card--back { left: 60px; top: 70px; }
  .card--front { left: 580px; top: 410px; }

  .watermark-ring {
    position: absolute;
    border-radius: 50%;
    border: 28px solid var(--watermark);
  }
  .card--back .watermark-ring { width: 300px; height: 300px; left: 130px; top: 10px; }
  .card--front .watermark-ring { width: 260px; height: 260px; right: -30px; top: -40px; }

  .brand {
    position: absolute;
    display: flex;
    align-items: center;
    gap: 14px;
  }
  .brand-dot {
    width: 58px; height: 58px;
    border-radius: 50%;
    border: 5px solid currentColor;
    flex: none;
  }
  .brand-rule {
    width: 1px; height: 64px;
    background: currentColor;
    flex: none;
  }
  .brand-name {
    font-weight: 700;
    font-size: 26px;
    line-height: 1.05;
    letter-spacing: 1.5px;
    text-transform: uppercase;
  }
  .card--back .brand { left: 160px; top: 100px; color: var(--emboss); }
  .card--front .brand { left: 44px; top: 62px; color: var(--brand-gray); }

  .tagline {
    position: absolute;
    left: 0; right: 0; top: 215px;
    text-align: center;
    color: var(--brand-blue);
    font-size: 15px;
    letter-spacing: 0.3px;
  }

  .corner-band {
    position: absolute;
    left: 0; top: 96px;
    width: 96px; height: 150px;
  }

  .address {
    position: absolute;
    right: 24px; top: 150px;
    text-align: right;
    color: var(--text-gray);
    font-size: 12.5px;
    font-style: normal;
    line-height: 1.55;
  }

  .person { position: absolute; left: 130px; top: 196px; }
  .person-name { color: var(--brand-blue); font-size: 18px; font-weight: 700; }
  .person-name sup { font-size: 9px; }
  .person-title { color: var(--text-gray); font-size: 13px; margin-top: 2px; }

  .divider-h {
    position: absolute;
    left: 130px; top: 250px;
    width: 406px; height: 1px;
    background: var(--rule-gray);
  }

  .contact { position: absolute; left: 130px; top: 262px; list-style: none; }
  .contact li {
    display: flex; align-items: center; gap: 10px;
    color: var(--text-gray); font-size: 13px; margin-bottom: 6px;
  }
  .contact svg { width: 18px; height: 18px; flex: none; }
</style>
</head>
<body>

  <section class="card card--back" aria-label="Card back">
    <div class="watermark-ring"></div>
    <div class="brand">
      <span class="brand-dot"></span>
      <span class="brand-rule"></span>
      <span class="brand-name">Keelbrook<br>Cover</span>
    </div>
    <p class="tagline">Your resource for life, long term care, and disability insurance</p>
  </section>

  <section class="card card--front" aria-label="Card front">
    <div class="watermark-ring"></div>
    <svg class="corner-band" viewBox="0 0 96 150" aria-hidden="true">
      <polygon points="0,30 96,0 96,150 0,150" fill="var(--brand-blue)"/>
    </svg>
    <div class="brand">
      <span class="brand-dot"></span>
      <span class="brand-rule"></span>
      <span class="brand-name">Keelbrook<br>Cover</span>
    </div>

    <address class="address">
      4620 W. Halvern Rd, Suite 300<br>
      Ashcombe Village, CO 80199
    </address>

    <div class="person">
      <p class="person-name">Owen T. Farrow, CLU<sup>®</sup>, LUTCF</p>
      <p class="person-title">President</p>
    </div>

    <div class="divider-h"></div>

    <ul class="contact">
      <li>
        <svg viewBox="0 0 18 18" aria-hidden="true">
          <circle cx="9" cy="9" r="8" fill="none" stroke="var(--brand-blue)" stroke-width="1.4"/>
          <path d="M6.2 5.2l1.4-.4.9 2-1 .8a5 5 0 0 0 2.6 2.6l.8-1 2 .9-.4 1.4c-3.6.2-6.5-2.7-6.3-6.3z" fill="var(--brand-blue)"/>
        </svg>
        (303) 555-0187
      </li>
      <li>
        <svg viewBox="0 0 18 18" aria-hidden="true">
          <circle cx="9" cy="9" r="8" fill="none" stroke="var(--brand-blue)" stroke-width="1.4"/>
          <rect x="5" y="6" width="8" height="6" fill="none" stroke="var(--brand-blue)" stroke-width="1.2"/>
          <path d="M5 6l4 3.2L13 6" fill="none" stroke="var(--brand-blue)" stroke-width="1.2"/>
        </svg>
        owen@keelbrookcover.example
      </li>
    </ul>
  </section>

</body>
</html>
```